Reach Crafters Unique Marketing Website Design

I am starting a new company that is a thought leader in the marketing consulting space. The company is called Reach Crafters. We intend to build a Wordpress site on the Astra Theme with the Spectra builder. Our goal is to become the leading voice that empowers high-ticket service business leaders to become Reach Crafters by equipping them with the cutting-edge frameworks and decision grade intelligence taught in leading business schools. What we are looking for is a website design that is clean and professional, making some use of white space well also being eye catching and distinctive in the consulting space. We will probably want to have a video on the homepage not in the hero section, but just below to explain the company and what we do. Our tagline is "Be found. Be chosen." I have attached a brand guide with some messaging, our typography choices, and our color system. The full site will have a primary nav that is four pages - About us, Services, Insights (essentially a blog), and Contact Us. The goal of this project is to develop an art direction that I can give to a designer to build loads of new pages.

Target Market(s)

Business owners (mostly male) from 30-60 years old, looking to fix their sales and marketing funnel.

Industry/Entity Type

Marketing consulting

Font styles to use
Sans Serif

Requirements
Must have
• A clean, professional design that builds trust with owners of high-ticket service businesses. We need a space for explainer video, and sections that tell prospects what we do. Would also like to have a blog carousel.
Nice to have
• Social feeds, if possible. See attached documents for colors and fonts.
Should not have
• Our feel is professional enough to be trustworthy, but unique enough to be memorable. Cartoon ideas do not meet the professional test, and we do not want the website to appear feminine.

```html
<!DOCTYPE html>
<html lang="en">
<head>
<meta charset="UTF-8">
<title>Reach Crafters – Predictable Demand For High-Ticket Growth</title>
<link rel="stylesheet" href="https://fonts.googleapis.com/css2?family=Oswald:wght@400;500;600&family=Inter:wght@400;500;600;700&display=swap">
<style>
:root{
  --navy:#0b1030;
  --navy-deep:#070a22;
  --blue:#2f4ef2;
  --green:#25c98a;
  --ink:#14162a;
  --body:#55586a;
  --lavender:#dcdcf7;
  --purple:#6a4de6;
  --charcoal:#2b2b2e;
  --white:#ffffff;
  --line:#e6e7ef;
}
*{box-sizing:border-box;margin:0;padding:0}
html,body{width:1200px;height:3904px;overflow:hidden}
body{font-family:"Inter",sans-serif;color:var(--body);background:var(--white);font-size:15px;line-height:1.6}
h1,h2,h3,.logo{font-family:"Oswald",sans-serif;font-weight:500;color:var(--ink)}
a{color:inherit;text-decoration:none}
.btn{display:inline-block;background:var(--blue);color:var(--white);font-family:"Inter",sans-serif;font-weight:700;font-size:13px;letter-spacing:.04em;text-transform:uppercase;padding:14px 22px;border-radius:6px}
.section-title{text-align:center;font-size:44px;line-height:1.2}
.section-title span{color:var(--blue)}
.title-rule{width:70px;height:4px;background:var(--green);margin:14px auto 0}

/* Hero */
.hero{position:relative;height:660px;background:radial-gradient(ellipse at 78% 55%,#1f3fa8 0%,#101a5a 35%,var(--navy) 70%);overflow:hidden}
.hero-visual{position:absolute;right:0;top:0;width:720px;height:660px;background:linear-gradient(135deg,rgba(60,110,255,.05),rgba(70,140,255,.35) 60%,rgba(20,40,120,.2))}
.nav{position:absolute;top:0;left:0;right:0;height:80px;display:flex;align-items:center;padding:0 112px}
.logo{color:var(--white);font-size:30px;letter-spacing:.02em}
.nav-links{margin-left:auto;display:flex;gap:30px;align-items:center;color:var(--white);font-size:15px}
.nav-links .active{position:relative;color:#7fa0ff}
.nav-links .active::after{content:"";position:absolute;left:0;right:0;bottom:-6px;height:2px;background:#7fa0ff}
.nav-links .btn{padding:12px 18px;font-size:13px}
.hero-copy{position:absolute;left:112px;top:148px;width:660px}
.tagline{display:block;color:var(--green);font-size:14px;font-weight:600;letter-spacing:.14em;text-transform:uppercase;margin-bottom:14px}
.hero h1{font-size:56px;line-height:1.25;color:var(--white);font-weight:500}
.hero h1 span{color:var(--green)}
.hero p{color:#dfe3f5;font-size:16px;margin:26px 0 30px;width:460px}

/* About + explainer video */
.about{position:relative;height:660px}
.about-video{position:absolute;left:112px;top:100px;width:448px;height:440px;background:linear-gradient(135deg,#c8ccd8,#8d93a6 60%,#5f6578)}
.play-btn{position:absolute;left:50%;top:50%;transform:translate(-50%,-50%);width:84px;height:84px;border-radius:50%;background:rgba(255,255,255,.92);display:flex;align-items:center;justify-content:center}
.video-label{position:absolute;left:0;right:0;bottom:0;padding:14px 20px;background:rgba(11,16,48,.72);color:var(--white);font-size:13px;font-weight:600;letter-spacing:.04em}
.about-badge{position:absolute;left:120px;top:108px;width:60px;height:60px;border-radius:50%;background:var(--blue);display:flex;align-items:center;justify-content:center}
.about-text{position:absolute;left:640px;top:100px;width:450px}
.about-text h2{font-size:48px}
.about-text h2 span{color:var(--blue)}
.about-text .rule{width:70px;height:4px;background:var(--green);margin:8px 0 22px}
.about-text p{font-size:14px;margin-bottom:14px}

/* Services */
.services{position:relative;height:640px;background:var(--lavender);padding-top:56px}
.service-grid{position:absolute;top:152px;left:112px;display:flex;gap:16px}
.service-card{position:relative;width:316px;height:408px;overflow:hidden;border-radius:4px}
.service-card .photo{position:absolute;inset:0}
.service-card h3{position:absolute;left:0;right:0;bottom:22px;text-align:center;color:var(--white);font-size:22px;font-weight:500}
.service-card.featured .photo{height:210px}
.service-card.featured .panel{position:absolute;left:0;right:0;top:190px;bottom:0;background:var(--purple);padding:52px 30px 0;text-align:center;color:#e5e0ff}
.service-card.featured .panel h3{position:static;font-size:22px;margin-bottom:10px}
.service-card.featured .panel p{font-size:13px}
.panel-icon{position:absolute;left:50%;top:-26px;transform:translateX(-50%);width:52px;height:52px;border-radius:50%;background:var(--white);display:flex;align-items:center;justify-content:center}
.slider-arrow{position:absolute;top:348px;width:22px;height:22px;border-radius:50%;display:flex;align-items:center;justify-content:center}
.slider-arrow.left{left:38px;background:var(--blue)}
.slider-arrow.right{right:38px;background:#a9abc2}
.dots{position:absolute;top:574px;left:0;right:0;display:flex;justify-content:center;gap:8px}
.dots i{width:8px;height:8px;border-radius:50%;background:#9ea0c4}
.dots i.on{background:var(--ink)}

/* Why */
.why{height:460px;padding-top:88px}
.why-grid{display:flex;justify-content:space-between;margin:72px 112px 0}
.why-item{width:300px}
.why-head{display:flex;align-items:center;gap:16px;margin-bottom:16px}
.why-icon{flex:none;width:44px;height:44px;border-radius:50%;display:flex;align-items:center;justify-content:center}
.why-head h3{font-family:"Inter",sans-serif;font-size:16px;font-weight:600;line-height:1.35}
.why-item p{font-size:13.5px}

/* Testimonials */
.testimonials{position:relative;height:380px;background:var(--charcoal);padding-top:66px}
.testimonials .section-title{color:var(--white);font-size:40px}
.testimonials .section-title span{color:var(--blue)}
.quote-row{display:flex;margin:42px 112px 0}
.quote{width:488px;padding-right:40px}
.quote + .quote{border-left:2px dashed #6a6a70;padding-left:40px}
.quote-head{display:flex;align-items:center;gap:16px;margin-bottom:16px}
.avatar{width:56px;height:56px;border-radius:50%;background:linear-gradient(135deg,#c9b7a3,#7d6a5a)}
.quote-head strong{display:block;color:var(--white);font-weight:500;font-size:15px}
.stars{color:#f5b400;font-size:13px;letter-spacing:2px}
.quote p{color:#d9d9de;font-size:13.5px;font-style:italic}
.testimonials .slider-arrow{top:210px}
.testimonials .slider-arrow.right{background:#5a5a62}

/* Blog */
.blog{height:780px;padding-top:110px}
.blog-grid{display:flex;gap:28px;margin:50px 112px 0}
.post{width:312px}
.post .thumb{height:252px;margin-bottom:22px}
.post .cat{color:var(--blue);font-weight:600;font-size:14px}
.post h3{font-family:"Inter",sans-serif;font-weight:500;font-size:20px;line-height:1.4;margin:6px 0 18px}
.meta{display:flex;gap:30px;font-size:12px;color:#8a8c9c;align-items:center}
.meta span{display:flex;align-items:center;gap:6px}

/* Footer */
.footer{position:relative;height:324px;background:var(--navy-deep);color:#c9cce0}
.footer-inner{display:flex;padding:44px 112px 0}
.footer-brand{width:432px}
.footer-brand .logo{color:#5f86ff;font-size:34px;display:block;margin-bottom:22px}
.subscribe-input{width:320px;height:44px;border-radius:4px;background:var(--white);color:#8a8c9c;font-size:13px;padding:12px 16px;margin-bottom:14px}
.footer .btn{padding:12px 18px;font-size:12px}
.socials{display:flex;gap:10px;margin-top:14px}
.socials i{width:28px;height:28px;border-radius:50%;background:var(--white)}
.footer-col{width:150px;font-size:12.5px}
.footer-col h4{color:var(--white);font-size:13px;font-weight:700;letter-spacing:.04em;margin-bottom:14px}
.footer-col li{list-style:none;line-height:1.85}
.footer-contact{width:200px;font-size:12.5px}
.footer-contact h4{color:var(--white);font-size:13px;font-weight:700;letter-spacing:.04em;margin-bottom:14px}
.contact-line{display:flex;align-items:center;gap:10px;margin-bottom:24px}
.contact-line b{flex:none;width:24px;height:24px;border-radius:50%;background:var(--blue);display:flex;align-items:center;justify-content:center}
.copyright{position:absolute;left:0;right:0;bottom:0;height:44px;border-top:1px solid #23284a;text-align:center;font-size:12px;line-height:44px}
</style>
</head>
<body>

<header class="hero">
  <div class="hero-visual" role="img" aria-label="Glowing blue growth chart with rising bars and arrow"></div>
  <nav class="nav">
    <a class="logo" href="#">REACH CRAFTERS</a>
    <div class="nav-links">
      <a class="active" href="#">Home</a>
      <a href="#">About Us</a>
      <a href="#">Services</a>
      <a href="#">Insights</a>
      <a class="btn" href="#">Contact Us</a>
    </div>
  </nav>
  <div class="hero-copy">
    <span class="tagline">Be found. Be chosen.</span>
    <h1><span>Predictable Demand</span> For<br>High-Ticket Growth</h1>
    <p>We help leaders replace guesswork with structured demand systems that scale revenue and authority.</p>
    <a class="btn" href="#">Start Your Demand Strategy</a>
  </div>
</header>

<section class="about">
  <div class="about-video" role="img" aria-label="Explainer video: consultant introducing Reach Crafters and what we do">
    <div class="play-btn"><svg width="30" height="30" viewBox="0 0 30 30"><path d="M9 5v20l17-10z" fill="#2f4ef2"/></svg></div>
    <div class="video-label">Watch: What Reach Crafters Does (2:14)</div>
  </div>
  <div class="about-badge">
    <svg width="28" height="28" viewBox="0 0 28 28"><circle cx="14" cy="14" r="11" fill="none" stroke="#fff" stroke-width="2.5"/><circle cx="14" cy="14" r="5" fill="#fff"/></svg>
  </div>
  <div class="about-text">
    <h2>About <span>Us</span></h2>
    <div class="rule"></div>
    <p>Reach Crafters is a marketing consulting firm built to serve ambitious service business leaders who want more than tactics — they want sustainable, predictable growth.</p>
    <p>We operate at the intersection of strategy, market intelligence, and execution. Our work is grounded in proven business frameworks and modern demand science, giving our clients the ability to make confident, high-impact decisions in increasingly competitive markets.</p>
    <p>We don't chase trends.<br>We build demand engines.</p>
    <a class="btn" href="#" style="margin-top:8px">Read More</a>
  </div>
</section>

<section class="services">
  <h2 class="section-title">Our <span>Services</span></h2>
  <div class="title-rule"></div>
  <div class="slider-arrow left"><svg width="10" height="10" viewBox="0 0 10 10"><path d="M6.5 1.5 3 5l3.5 3.5" fill="none" stroke="#fff" stroke-width="1.6"/></svg></div>
  <div class="service-grid">
    <article class="service-card">
      <div class="photo" role="img" aria-label="Advisors meeting around a table" style="background:linear-gradient(180deg,#8b7768 0%,#4a3c33 60%,#1c1612 100%)"></div>
      <h3>Leadership Advisory &amp; Consulting</h3>
    </article>
    <article class="service-card featured">
      <div class="photo" role="img" aria-label="Supply and demand concept on blocks" style="background:linear-gradient(135deg,#3f6fd8,#1c2d74)"></div>
      <div class="panel">
        <div class="panel-icon"><svg width="24" height="24" viewBox="0 0 24 24"><circle cx="12" cy="10" r="5" fill="none" stroke="#25c98a" stroke-width="2"/><path d="M12 15v6M9 21h6" stroke="#25c98a" stroke-width="2"/></svg></div>
        <h3>Demand Strategy &amp; Positioning</h3>
        <p>Sharpen your market position and build a clear plan that turns attention into qualified demand.</p>
      </div>
    </article>
    <article class="service-card">
      <div class="photo" role="img" aria-label="Rising digital bar chart in blue light" style="background:linear-gradient(180deg,#7fc2ea 0%,#2f78c4 55%,#0c2a5c 100%)"></div>
      <h3>Growth Architecture</h3>
    </article>
  </div>
  <div class="slider-arrow right"><svg width="10" height="10" viewBox="0 0 10 10"><path d="M3.5 1.5 7 5 3.5 8.5" fill="none" stroke="#fff" stroke-width="1.6"/></svg></div>
  <div class="dots"><i></i><i class="on"></i><i></i></div>
</section>

<section class="why">
  <h2 class="section-title">Why <span>Choose Us</span></h2>
  <div class="title-rule"></div>
  <div class="why-grid">
    <div class="why-item">
      <div class="why-head">
        <div class="why-icon" style="background:var(--blue)"><svg width="20" height="20" viewBox="0 0 20 20"><path d="M4 15V9M9 15V5M14 15V11" stroke="#fff" stroke-width="2.5"/></svg></div>
        <h3>Decision-Grade Intelligence</h3>
      </div>
      <p>We replace gut-feel marketing with structured market data, demand signals, and buyer behavior insights.</p>
    </div>
    <div class="why-item">
      <div class="why-head">
        <div class="why-icon" style="background:var(--green)"><svg width="20" height="20" viewBox="0 0 20 20"><path d="M4 10.5 8 14.5 16 6" fill="none" stroke="#fff" stroke-width="2.5"/></svg></div>
        <h3>Elite Growth Frameworks</h3>
      </div>
      <p>Our methods are inspired by leading MBA-level strategy models adapted for real-world execution.</p>
    </div>
    <div class="why-item">
      <div class="why-head">
        <div class="why-icon" style="background:var(--blue)"><svg width="20" height="20" viewBox="0 0 20 20"><path d="M10 3 12 8h5l-4 3 1.5 5L10 13l-4.5 3L7 11 3 8h5z" fill="#fff"/></svg></div>
        <h3>Built For High-Ticket Services</h3>
      </div>
      <p>We specialize in complex sales cycles, premium positioning, and authority-based demand.</p>
    </div>
  </div>
</section>

<section class="testimonials">
  <h2 class="section-title"><span>What Leaders Say</span> About Reach Crafters</h2>
  <div class="title-rule"></div>
  <div class="slider-arrow left"><svg width="10" height="10" viewBox="0 0 10 10"><path d="M6.5 1.5 3 5l3.5 3.5" fill="none" stroke="#fff" stroke-width="1.6"/></svg></div>
  <div class="quote-row">
    <div class="quote">
      <div class="quote-head">
        <div class="avatar" role="img" aria-label="Portrait of a B2B consulting firm founder"></div>
        <div><strong>Founder, B2B Consulting Firm</strong><span class="stars">★★★★★</span></div>
      </div>
      <p>"Reach Crafters helped us move from scattered marketing tactics to a real demand strategy. For the first time, we have clarity on our positioning, pipeline, and growth roadmap."</p>
    </div>
    <div class="quote">
      <div class="quote-head">
        <div class="avatar" role="img" aria-label="Portrait of a high-ticket service brand CEO"></div>
        <div><strong>CEO, High-Ticket Service Brand</strong><span class="stars">★★★★★</span></div>
      </div>
      <p>"Within 90 days, we saw a clear increase in qualified inbound leads and stronger deal quality. The frameworks Reach Crafters uses are unlike anything we've experienced."</p>
    </div>
  </div>
  <div class="slider-arrow right"><svg width="10" height="10" viewBox="0 0 10 10"><path d="M3.5 1.5 7 5 3.5 8.5" fill="none" stroke="#fff" stroke-width="1.6"/></svg></div>
</section>

<section class="blog">
  <h2 class="section-title">Our <span>Blog</span></h2>
  <div class="title-rule"></div>
  <div class="blog-grid">
    <article class="post">
      <div class="thumb" role="img" aria-label="Team reviewing charts on a whiteboard" style="background:linear-gradient(135deg,#d9d3ca,#8f7f70)"></div>
      <div class="cat">Strategy</div>
      <h3>The Demand Gap: Why Most Service Businesses Struggle To Scale</h3>
      <div class="meta"><span><svg width="12" height="12" viewBox="0 0 12 12"><rect x="1" y="2" width="10" height="9" fill="none" stroke="#8a8c9c"/><path d="M1 5h10" stroke="#8a8c9c"/></svg>Jan 27,2024</span><span><svg width="12" height="12" viewBox="0 0 12 12"><path d="M1 2h10v6H5l-3 3V8H1z" fill="none" stroke="#8a8c9c"/></svg>4 Comments</span></div>
    </article>
    <article class="post">
      <div class="thumb" role="img" aria-label="Colleagues collaborating in a meeting" style="background:linear-gradient(135deg,#c4502f,#5c2a1f)"></div>
      <div class="cat">Growth Systems</div>
      <h3>How High-Ticket Services Can Build Predictable Demand Without Paid Ads</h3>
      <div class="meta"><span><svg width="12" height="12" viewBox="0 0 12 12"><rect x="1" y="2" width="10" height="9" fill="none" stroke="#8a8c9c"/><path d="M1 5h10" stroke="#8a8c9c"/></svg>Jan 27,2024</span><span><svg width="12" height="12" viewBox="0 0 12 12"><path d="M1 2h10v6H5l-3 3V8H1z" fill="none" stroke="#8a8c9c"/></svg>4 Comments</span></div>
    </article>
    <article class="post">
      <div class="thumb" role="img" aria-label="Business team discussing around a laptop" style="background:linear-gradient(135deg,#b9c4d4,#3e4f6d)"></div>
      <div class="cat">Demand Intelligence</div>
      <h3>The Demand Gap: Why Most Service Businesses Struggle To Scale</h3>
      <div class="meta"><span><svg width="12" height="12" viewBox="0 0 12 12"><rect x="1" y="2" width="10" height="9" fill="none" stroke="#8a8c9c"/><path d="M1 5h10" stroke="#8a8c9c"/></svg>Jan 27,2024</span><span><svg width="12" height="12" viewBox="0 0 12 12"><path d="M1 2h10v6H5l-3 3V8H1z" fill="none" stroke="#8a8c9c"/></svg>4 Comments</span></div>
    </article>
  </div>
</section>

<footer class="footer">
  <div class="footer-inner">
    <div class="footer-brand">
      <span class="logo">REACH CRAFTERS</span>
      <div class="subscribe-input">Enter Email Address</div>
      <a class="btn" href="#">Subscribe</a>
      <div class="socials"><i></i><i></i><i></i><i></i></div>
    </div>
    <div class="footer-col">
      <h4>QUICK LINKS</h4>
      <ul><li>Home</li><li>About Us</li><li>Services</li><li>Insights</li><li>Testimonials</li><li>Contact Us</li></ul>
    </div>
    <div class="footer-col">
      <h4>OTHER LINKS</h4>
      <ul><li>Privacy Policy</li><li>Terms &amp; Conditions</li><li>Disclaimer</li><li>Faq's</li><li>Support</li><li>Help</li></ul>
    </div>
    <div class="footer-contact">
      <h4>CONTACT INFO</h4>
      <div class="contact-line"><b><svg width="12" height="12" viewBox="0 0 12 12"><path d="M6 11S2 7 2 4.5a4 4 0 0 1 8 0C10 7 6 11 6 11z" fill="#fff"/></svg></b>Lorem Ipsum, USA - 43759</div>
      <div class="contact-line"><b><svg width="12" height="12" viewBox="0 0 12 12"><path d="M2 1h3l1 3-1.5 1a6 6 0 0 0 2.5 2.5L8 6l3 1v3c0 .6-.4 1-1 1A9 9 0 0 1 1 2c0-.6.4-1 1-1z" fill="#fff"/></svg></b>+1 000 000 0000</div>
      <div class="contact-line"><b><svg width="12" height="12" viewBox="0 0 12 12"><rect x="1" y="2.5" width="10" height="7" fill="none" stroke="#fff"/><path d="M1 3l5 4 5-4" fill="none" stroke="#fff"/></svg></b>info@reachcrafters.com</div>
    </div>
  </div>
  <div class="copyright">© 2026 Reach Crafters All Rights Reserved</div>
</footer>

</body>
</html>
```